Plakat für Tanzschule
Zielgruppe
Wir sind eine Tanzschule
Hallo,
ich benötige ein professionelles Design für ein Schild im Format 2 Meter breit × 1 Meter hoch (Querformat), das von einem stark frequentierten Parkplatz aus gut sichtbar ist.
✅ Ziel:
Gestaltung eines aufmerksamkeitsstarken, eleganten und energiegeladenen Werbeschilds
Das Schild soll sofort zeigen, worum es geht (Tanzstile) und zum kostenlosen Schnuppern motivieren
Die Gestaltung soll hochwertig und grafisch modern wirken
Bild / Hintergrund:
Ich habe einen ersten Design-Vorschlag hochgeladen (Screenshot)
⚠️ Ursprünglich hatte ich vor, ein bereits ausgeschnittenes und bearbeitetes Bild zu liefern (z. B. Unreinheiten und Störungen im Bild zu glätten oder zu entfernt und Zähne etwas weißer). Das kann ich jetzt leider doch nicht nachreichen. Daher müsste doch die Bearbeitung des Bildes mit übernommen werden.
✏️ Textinhalte (hierarchisch sortiert):
TANZSCHULE
Salsa · Bachata · Kizomba · Zouk
Jetzt Gratis Schnuppern!
Ritmo del Faro (Markenname)
www.ritmo-del-faro.de
???? Wichtig:
Die wichtigsten Inhalte (Tanzarten & CTA) müssen sofort erfassbar sein
Design bitte auf Fernwirkung, klare Lesbarkeit und modernes visuelles Layout ausrichten
Text in sinnvollen Größenabstufungen und mit sauberer visueller Hierarchie
Unsere eigentliche Hauptfarbe ist #ad194f, bis jetzt habe ich aber noch keine schöne Möglichkeit gefunden, in das aktuelle Design einzuarbeiten.
????️ Endformat & Übergabe:
Bitte das fertige Layout als .afdesign Datei (Affinity Designer) liefern
Optional PSD, EPS

```html
<!DOCTYPE html>
<html lang="de">
<head>
<meta charset="utf-8">
<title>Ritmo del Faro – Tanzschule Banner</title>
<link rel="stylesheet" href="https://fonts.googleapis.com/css2?family=Oswald:wght@600&family=Open+Sans:wght@300;400;700&display=swap">
<style>
  :root {
    --page-bg: #f3f3f3;
    --banner-base: #4a4746;
    --banner-band: #393736;
    --banner-swoosh: #3f3d3c;
    --banner-light: #e9e8e8;
    --brand-berry: #ad194f;
    --text-light: #ededed;
    --text-dark: #333232;
  }
  html, body {
    margin: 0;
    width: 1200px;
    height: 900px;
    overflow: hidden;
    background: var(--page-bg);
  }
  .banner {
    position: absolute;
    left: 50px;
    top: 175px;
    width: 1100px;
    height: 548px;
    box-shadow: 0 10px 30px rgba(0,0,0,0.18);
  }
  .banner svg { display: block; width: 100%; height: 100%; }
  .headline { font-family: "Oswald", sans-serif; font-weight: 600; fill: var(--text-light); }
  .brand-name { font-family: "Open Sans", sans-serif; font-weight: 300; fill: var(--text-light); }
  .brand-tagline { font-family: "Open Sans", sans-serif; font-weight: 300; fill: var(--text-light); }
  .cta-text { font-family: "Open Sans", sans-serif; font-weight: 700; fill: #ffffff; }
  .web-address { font-family: "Open Sans", sans-serif; font-weight: 400; fill: var(--text-dark); }
</style>
</head>
<body>
  <div class="banner">
    <svg viewBox="0 0 1365 680" xmlns="http://www.w3.org/2000/svg">
      <defs>
        <linearGradient id="dancers-tone" x1="0" y1="0" x2="1" y2="1">
          <stop offset="0" stop-color="#8a7a66"/>
          <stop offset="0.55" stop-color="#6f6964"/>
          <stop offset="1" stop-color="#566358"/>
        </linearGradient>
      </defs>

      <!-- background -->
      <rect class="bg-base" width="1365" height="680" fill="var(--banner-base)"/>
      <path class="bg-band" d="M0,640 C200,470 420,360 700,332 C950,310 1180,335 1365,372 L1365,680 L0,680 Z" fill="var(--banner-band)"/>
      <path class="bg-light-wave" d="M690,680 C840,600 1090,550 1365,605 L1365,680 Z" fill="var(--banner-light)"/>

      <!-- dancing couple photo -->
      <rect class="dancers-photo" x="0" y="24" width="680" height="656"
            fill="url(#dancers-tone)" role="img"
            aria-label="Foto: lachendes Tanzpaar beim Salsa, Frau mit wehendem blondem Haar und weißem Top, Mann mit Brille und grünem T-Shirt"/>

      <!-- brand -->
      <g class="brand">
        <text class="brand-name" x="960" y="100" text-anchor="middle" font-size="40">Ritmo del Faro</text>
        <text class="brand-tagline" x="960" y="128" text-anchor="middle" font-size="16">Salsa · Bachata · Kizomba</text>
        <circle class="brand-dot" cx="1100" cy="86" r="16" fill="var(--brand-berry)"/>
      </g>

      <!-- headline -->
      <text class="headline headline-main" x="1010" y="283" text-anchor="middle" font-size="126" textLength="605" lengthAdjust="spacingAndGlyphs">TANZSCHULE</text>
      <text class="headline dance-styles" x="1015" y="442" text-anchor="middle" font-size="78" textLength="530" lengthAdjust="spacingAndGlyphs">SALSA · BACHATA</text>
      <text class="headline dance-styles" x="1015" y="522" text-anchor="middle" font-size="78" textLength="500" lengthAdjust="spacingAndGlyphs">KIZOMBA · ZOUK</text>

      <!-- call to action -->
      <g class="cta-badge">
        <circle cx="583" cy="527" r="125" fill="var(--brand-berry)"/>
        <g transform="rotate(-10 583 527)">
          <text class="cta-text" x="583" y="490" text-anchor="middle" font-size="30">Jetzt</text>
          <text class="cta-text" x="583" y="535" text-anchor="middle" font-size="46">Gratis</text>
          <text class="cta-text" x="583" y="572" text-anchor="middle" font-size="30">Schnuppern!</text>
        </g>
      </g>

      <!-- web address -->
      <text class="web-address" x="1015" y="640" text-anchor="middle" font-size="27">www.ritmo-del-faro.de</text>
    </svg>
  </div>
</body>
</html>
```